Maple Gable Business Card

Colors can be blue, grey and white as you see in the attached logo. Needs to have a spot for name, title, phone, email, address, and website. There also needs to be a spot for an agent's picture.

Contact Information for Business Card

See project description.

Colors

Designer to choose colors to be used in the design.

```html
<!DOCTYPE html>
<html lang="en">
<head>
<meta charset="utf-8">
<title>Maple Gable Business Card</title>
<link rel="stylesheet" href="https://fonts.googleapis.com/css2?family=Roboto:wght@400;500;700&display=swap">
<style>
  :root {
    --backdrop: #2a2a2b;
    --card: #232426;
    --blue: #2f80c8;
    --text: #dcdcdc;
    --rule: #77787a;
  }
  * { box-sizing: border-box; margin: 0; padding: 0; }
  html, body {
    width: 1200px; height: 1108px; overflow: hidden;
    background: var(--backdrop);
    font-family: "Roboto", sans-serif;
  }
  .stage {
    position: relative; width: 1200px; height: 1108px;
    display: flex; justify-content: center; align-items: center; gap: 70px;
  }
  .card {
    width: 390px; height: 650px;
    background: var(--card);
    border-radius: 22px;
    box-shadow: 0 14px 40px rgba(0,0,0,.45);
    overflow: hidden;
    position: relative;
  }
  .agent-photo {
    height: 330px;
    margin: 0 40px;
    background: radial-gradient(ellipse at 50% 30%, #5a5c62 0%, #2e3034 55%, var(--card) 80%);
  }
  .front-body { text-align: center; color: var(--text); }
  .agent-name { color: var(--blue); font-weight: 500; font-size: 32px; margin-top: 4px; }
  .agent-title { font-size: 22px; margin-top: 2px; }
  .icon-rule { display: flex; align-items: center; gap: 8px; margin: 10px 38px 12px; }
  .icon-rule .line { flex: 1; height: 1px; background: var(--rule); }
  .icon {
    width: 26px; height: 26px; border-radius: 50%;
    background: var(--blue); display: flex; align-items: center; justify-content: center;
  }
  .contact-list { list-style: none; font-size: 22px; line-height: 1.35; }
  .contact-list .accent { color: var(--blue); }
  .plain-rule { height: 1px; background: var(--rule); margin: 16px 38px 14px; }
  .address { font-size: 22px; line-height: 1.35; }
  .back { display: flex; align-items: center; justify-content: center; }
  .brand { display: flex; flex-direction: column; align-items: center; gap: 10px; }
  .brand-mark { width: 34px; height: 34px; background: var(--blue); }
  .brand-name {
    color: var(--blue); font-weight: 500; font-size: 36px;
    letter-spacing: 1px; text-transform: uppercase;
  }
  .brand-sub {
    color: var(--blue); font-weight: 500; font-size: 16px;
    letter-spacing: 5px; text-transform: uppercase;
  }
</style>
</head>
<body>
<main class="stage">
  <section class="card front">
    <div class="agent-photo" role="img" aria-label="Portrait photo of the agent in a dark suit"></div>
    <div class="front-body">
      <h1 class="agent-name">Daniel Reyes</h1>
      <p class="agent-title">Manager</p>
      <div class="icon-rule">
        <span class="line"></span>
        <span class="icon"><svg width="14" height="14" viewBox="0 0 24 24"><path fill="#fff" d="M6.6 10.8a15 15 0 0 0 6.6 6.6l2.2-2.2c.3-.3.7-.4 1-.2 1.1.4 2.3.6 3.6.6.6 0 1 .4 1 1V20c0 .6-.4 1-1 1A17 17 0 0 1 3 4c0-.6.4-1 1-1h3.5c.6 0 1 .4 1 1 0 1.3.2 2.5.6 3.6.1.3 0 .7-.2 1z"/></svg></span>
        <span class="icon"><svg width="14" height="14" viewBox="0 0 24 24"><rect x="3" y="6" width="18" height="12" rx="1" fill="#fff"/><path d="M3 6l9 7 9-7" fill="none" stroke="#2f80c8" stroke-width="2"/></svg></span>
        <span class="icon"><svg width="14" height="14" viewBox="0 0 24 24" fill="none" stroke="#fff" stroke-width="2"><circle cx="12" cy="12" r="9"/><path d="M3 12h18M12 3c3 3 3 15 0 18M12 3c-3 3-3 15 0 18"/></svg></span>
        <span class="line"></span>
      </div>
      <ul class="contact-list">
        <li>555-018-3427</li>
        <li>youremail@mailbox.com</li>
        <li>www.<span class="accent">yourwebsite</span>.com</li>
      </ul>
      <div class="plain-rule"></div>
      <p class="address">Your address, city<br>state, ZIP 0000</p>
    </div>
  </section>
  <section class="card back">
    <div class="brand">
      <span class="brand-mark"></span>
      <span class="brand-name">Maple Gable</span>
      <span class="brand-sub">Real Estate</span>
    </div>
  </section>
</main>
</body>
</html>
```